Business Card for a Dental Office

The design should communicate integrity, quality and reliability. We also want the card look elegant, simple, but still stand out, different from the traditional-dental-office business card.

Industry/Entity Type

Business

```html
<!DOCTYPE html>
<html lang="en">
<head>
<meta charset="utf-8">
<title>Lakeview Dental – Business Card</title>
<link href="https://fonts.googleapis.com/css2?family=Montserrat:wght@500&family=Open+Sans:wght@400;700&display=swap" rel="stylesheet">
<style>
  :root {
    --backdrop: #e6e6e4;
    --card: #ffffff;
    --gold: #b3972a;
    --charcoal: #3a3a3c;
    --ink: #1d1d1d;
    --divider: #b8b8b8;
  }
  html, body {
    margin: 0;
    width: 1200px;
    height: 977px;
    overflow: hidden;
    background: var(--backdrop);
  }
  .card {
    position: absolute;
    left: 150px;
    top: 231px;
    width: 900px;
    height: 515px;
    background: var(--card);
    box-shadow: 0 12px 30px rgba(0,0,0,0.18);
    overflow: hidden;
  }
  .card-accents {
    position: absolute;
    inset: 0;
  }
  .contact-block {
    position: absolute;
    left: 150px;
    top: 138px;
    font-family: "Open Sans", sans-serif;
    color: var(--ink);
  }
  .person-name {
    font-family: "Montserrat", sans-serif;
    font-weight: 500;
    font-size: 30px;
    color: var(--gold);
    margin: 0;
    line-height: 1.1;
  }
  .person-role {
    font-weight: 700;
    font-size: 16px;
    margin: 2px 0 30px 10px;
  }
  .detail {
    display: flex;
    align-items: flex-start;
    gap: 18px;
    font-size: 17px;
    line-height: 1.45;
    margin-left: 34px;
    white-space: nowrap;
  }
  .detail svg { flex: none; width: 18px; height: 18px; margin-top: 3px; fill: var(--gold); }
  .detail.address { margin-bottom: 22px; }
  .detail.stack { margin-bottom: 4px; }
  .divider {
    position: absolute;
    left: 455px;
    top: 130px;
    width: 1.5px;
    height: 215px;
    background: linear-gradient(var(--divider), #d8d8d8);
  }
  .brand {
    position: absolute;
    left: 505px;
    top: 200px;
    display: flex;
    align-items: center;
    gap: 14px;
    font-family: "Open Sans", sans-serif;
    white-space: nowrap;
  }
  .brand-mark {
    width: 40px;
    height: 40px;
    background: var(--gold);
  }
  .brand-text { display: flex; flex-direction: column; }
  .brand-name {
    font-weight: 700;
    font-size: 24px;
    letter-spacing: 0.5px;
    color: var(--ink);
    text-transform: uppercase;
    line-height: 1.1;
  }
  .brand-tagline {
    font-weight: 700;
    font-size: 10.5px;
    letter-spacing: 0.6px;
    color: var(--gold);
    text-transform: uppercase;
  }
</style>
</head>
<body>
  <section class="card">
    <svg class="card-accents" viewBox="0 0 900 515" width="900" height="515" aria-hidden="true">
      <path fill="var(--charcoal)" d="M0 30 H28 Q52 30 58 52 L124 440 Q130 470 112 490 L90 515 H0 Z"/>
      <path fill="var(--gold)" d="M816 0 H900 V315 H884 Q864 315 860 290 L832 60 Q828 30 816 0 Z"/>
    </svg>

    <div class="contact-block">
      <h1 class="person-name">Daniel Hart</h1>
      <div class="person-role">Manager</div>

      <div class="detail address">
        <svg viewBox="0 0 24 24"><path d="M12 2a7 7 0 0 0-7 7c0 5 7 13 7 13s7-8 7-13a7 7 0 0 0-7-7zm0 9.5A2.5 2.5 0 1 1 12 6.5a2.5 2.5 0 0 1 0 5z"/></svg>
        <span>1234 Harbor Lane,<br>CA 95017</span>
      </div>
      <div class="detail stack">
        <svg viewBox="0 0 24 24"><path d="M6.6 10.8a15 15 0 0 0 6.6 6.6l2.2-2.2a1 1 0 0 1 1-.25 11.4 11.4 0 0 0 3.6.57 1 1 0 0 1 1 1V20a1 1 0 0 1-1 1A17 17 0 0 1 3 4a1 1 0 0 1 1-1h3.5a1 1 0 0 1 1 1c0 1.25.2 2.45.57 3.57a1 1 0 0 1-.25 1z"/></svg>
        <span>(800) 555-0142</span>
      </div>
      <div class="detail stack">
        <svg viewBox="0 0 24 24"><path d="M2 5h20v14H2z M3 6l9 7 9-7" /></svg>
        <span>info@lakeviewdental.com</span>
      </div>
      <div class="detail stack">
        <svg viewBox="0 0 24 24"><circle cx="12" cy="12" r="10"/><path d="M2 12h20M12 2v20" stroke="#fff" stroke-width="1.5" fill="none"/></svg>
        <span>www.lakeviewdental.com</span>
      </div>
    </div>

    <div class="divider"></div>

    <div class="brand">
      <div class="brand-mark"></div>
      <div class="brand-text">
        <span class="brand-name">Lakeview Dental</span>
        <span class="brand-tagline">Gentle care for every family</span>
      </div>
    </div>
  </section>
</body>
</html>
```